Harborview Estates Business Card for Apartment Buildings

Create business cards for resident managers who run apartment buildings. The audience is the public who are searching for apartment rentals, and current residents who live at the apartment building. Key design element will be incorporating the company logo, however, the logo cannot dominate. The building name and manager name are more important than the logo. Current business card design leaves little room for copy, so we may need to reduce the size on the current card to allow for more space for copy.

Target Market(s)

Adults 18-65 years of age, who are looking for an apartment rental, plus current residents who live at our apartment buildings.

Industry/Entity Type

Property Management

Contact Information for Business Card

A major design element will be use of the company logo. Important property and manager contact information must be part of the design. The size of the logo will need to be reduced to make room for building and manager contact copy.

Font styles to use
Sans Serif

Colors
3176b5
000000
959595
ffffff

Requirements
Must have
• 1) Incorporate the company logo.
• 2) Use the company colors (dark blue, black/grey, over white).
• 3) FEATURE THE BUILDING NAME
• 4) FEATURE THE MANAGER NAME
• 5) The company name is less important than BUILDING and MANAGER
• 6) Manager contact information
• **SEE ATTACHED CREATIVE BRIEF**
Nice to have
• 1) Back of card logo watermark
• 2) Ability to write notes on back of carfd
Should not have
• Avoid letting the company logo dominate the card, the building name and manager are more important than the company logo.

```html
<!DOCTYPE html>
<html lang="en">
<head>
<meta charset="utf-8">
<title>Harborview Estates – Resident Manager Card</title>
<link href="https://fonts.googleapis.com/css2?family=Roboto:wght@400;700&display=swap" rel="stylesheet">
<style>
  :root {
    --brand-blue: #0a68a8;
    --ink-grey: #444446;
    --text-grey: #4a4a4a;
    --soft-grey: #e4e5ea;
    --paper: #ffffff;
    --backdrop: #e8e8e8;
  }
  * { margin: 0; padding: 0; box-sizing: border-box; }
  html, body { width: 1200px; height: 960px; overflow: hidden; }
  body {
    background: var(--backdrop);
    font-family: "Roboto", Arial, sans-serif;
    position: relative;
  }
  .card {
    position: absolute;
    left: 280px;
    width: 656px;
    height: 374px;
    background: var(--paper);
    box-shadow: 0 3px 8px rgba(0,0,0,0.25);
    overflow: hidden;
  }
  .card--front { top: 80px; }
  .card--back { top: 506px; }

  .manager { position: absolute; left: 74px; top: 57px; z-index: 2; }
  .manager__name { font-size: 22px; font-weight: 700; color: var(--brand-blue); line-height: 1.1; }
  .manager__title { font-size: 16px; color: var(--text-grey); margin-top: 6px; }

  .property { position: absolute; left: 74px; top: 140px; z-index: 2; }
  .property__name { font-size: 15px; font-weight: 700; color: var(--brand-blue); margin-bottom: 6px; }
  .property__line { font-size: 15px; color: var(--text-grey); line-height: 22px; }

  .contact { position: absolute; left: 74px; top: 222px; list-style: none; z-index: 2; }
  .contact__item { display: flex; align-items: center; height: 22px; font-size: 15.5px; color: var(--text-grey); }
  .contact__icon { width: 16px; height: 14px; margin-right: 8px; fill: var(--brand-blue); }

  .company {
    position: absolute; right: 60px; top: 48px;
    display: flex; align-items: center; gap: 10px;
    color: var(--brand-blue); font-weight: 700; z-index: 2;
  }
  .company__square { width: 34px; height: 34px; background: var(--brand-blue); }
  .company__name { font-size: 28px; line-height: 1; letter-spacing: 0.5px; }
  .company__name small { display: block; font-size: 13px; letter-spacing: 3px; margin-top: 4px; }

  .watermark-ring {
    position: absolute; border-radius: 50%;
    border: 12px solid var(--soft-grey);
  }
  .card--front .watermark-ring { left: 350px; top: 150px; width: 250px; height: 250px; z-index: 0; }
  .card--back .watermark-ring { left: 208px; top: 64px; width: 250px; height: 250px; }

  .swoosh { position: absolute; left: 0; top: 0; width: 656px; height: 374px; z-index: 1; }
  .website {
    position: absolute; right: 60px; bottom: 13px;
    font-size: 14px; color: var(--paper); z-index: 2;
  }
</style>
</head>
<body>
  <section class="card card--front">
    <div class="watermark-ring"></div>

    <div class="manager">
      <h1 class="manager__name">Marisol Quintero</h1>
      <p class="manager__title">Resident Manager</p>
    </div>

    <div class="company">
      <span class="company__square"></span>
      <p class="company__name">HARBORVIEW<small>ESTATES LLC</small></p>
    </div>

    <div class="property">
      <h2 class="property__name">Bayside Court Apartments</h2>
      <p class="property__line">2485 Cedar Lane Street</p>
      <p class="property__line">Riverton, CA 90210</p>
    </div>

    <ul class="contact">
      <li class="contact__item">
        <svg class="contact__icon" viewBox="0 0 16 16"><path d="M4 1 L7 4 L5 6 Q7 10 10 11 L12 9 L15 12 L12 15 Q2 12 1 4 Z"/></svg>555-210-4417
      </li>
      <li class="contact__item">
        <svg class="contact__icon" viewBox="0 0 16 16"><path d="M1 5 Q8 0 15 5 L13 7 L11 6 L11 4 Q8 3 5 4 L5 6 L3 7 Z"/><rect x="3" y="8" width="10" height="7" rx="1"/></svg>555-210-4480
      </li>
      <li class="contact__item">
        <svg class="contact__icon" viewBox="0 0 16 16"><path d="M4 0 H12 V16 H4 Z M5.5 2 V12 H10.5 V2 Z" fill-rule="evenodd"/></svg>555-386-9152
      </li>
      <li class="contact__item">
        <svg class="contact__icon" viewBox="0 0 16 16"><path d="M1 3 H15 L8 9 Z M1 5 L6 9 L1 13 Z M15 5 L10 9 L15 13 Z M7 10 L8 11 L9 10 L14 14 H2 Z"/></svg>marisol@harborviewest.com
      </li>
    </ul>

    <svg class="swoosh" viewBox="0 0 656 374" aria-hidden="true">
      <path d="M0 316 Q300 350 610 292 Q300 376 0 338 Z" fill="var(--ink-grey)"/>
      <path d="M0 346 Q330 386 656 283 L656 374 L0 374 Z" fill="var(--brand-blue)"/>
    </svg>
    <p class="website">www.harborviewest.com</p>
  </section>

  <section class="card card--back">
    <div class="watermark-ring"></div>
  </section>
</body>
</html>
```